School Poster

Design so that these can be placed in classrooms across the school.

Attached is another design we have had done. Use a similar theme.

Consider using themes from https://corvalhs.edq.example.au/

please edit Binder1 doc.

Students and teachers

```html
<!DOCTYPE html>
<html lang="en">
<head>
<meta charset="utf-8">
<title>Classroom Posters – Corval High</title>
<link rel="stylesheet" href="https://fonts.googleapis.com/css2?family=Fira+Sans:wght@500;600;700;800;900&family=Fira+Sans+Condensed:wght@500;600;700&display=swap">
<style>
  :root{
    --navy:#1a3a7c;
    --navy-deep:#142d66;
    --yellow:#f9e26a;
    --cream:#fdf9e4;
    --ice:#e5effa;
    --white:#ffffff;
    --stage:#6b6b6b;
    --rule:#9fb5d6;
  }
  *{box-sizing:border-box;margin:0;padding:0}
  html,body{width:1200px;height:887px;overflow:hidden}
  body{background:var(--stage);font-family:"Fira Sans",sans-serif;color:var(--navy);position:relative}

  .poster{position:absolute;top:70px;width:524px;height:741px;overflow:hidden}
  .poster--help{left:59px}
  .poster--ai{left:619px}
  .poster-bg{position:absolute;inset:0;width:100%;height:100%}

  .brand{position:absolute;left:21px;top:34px;width:108px;display:flex;flex-direction:column;align-items:center;gap:8px}
  .brand-mark{width:60px;height:60px;border-radius:50%;background:var(--yellow)}
  .brand-name{font-weight:700;font-size:15px;color:var(--white);letter-spacing:.5px;text-align:center;line-height:1.1}

  .headline{position:absolute;left:145px;font-weight:900;color:var(--white);text-transform:uppercase;white-space:nowrap}
  .poster--help .headline{top:27px;font-size:46px;line-height:39px;letter-spacing:-.4px}
  .poster--ai .headline{top:29px;font-size:38px;line-height:33px;letter-spacing:-.7px}
  .subhead{position:absolute;left:146px;font-family:"Fira Sans Condensed",sans-serif;font-weight:600;color:var(--yellow);text-transform:uppercase;white-space:nowrap}
  .poster--help .subhead{top:115px;font-size:34px;line-height:34px}
  .poster--ai .subhead{top:105px;font-size:28px;line-height:26px}

  /* steps */
  .step{position:absolute;top:187px;width:131px;height:394px;border:3px solid var(--navy);border-radius:6px;background:var(--ice);overflow:hidden;display:flex;flex-direction:column}
  .step-art{height:90px;flex:0 0 90px;background:var(--cream);display:flex;align-items:center;justify-content:center}
  .step-art span{width:64px;height:64px;border-radius:10px;background:#ede6c4}
  .step-label{height:49px;flex:0 0 49px;background:var(--yellow);border-top:3px solid var(--navy);border-bottom:3px solid var(--navy);display:flex;align-items:center;justify-content:center;text-align:center;font-weight:800;font-size:16.5px;line-height:16.5px;text-transform:uppercase;white-space:nowrap}
  .step-body{padding:10px 3px 0 8px}
  .step-lead{font-weight:700;font-size:14px;line-height:15.5px;text-align:center;margin-bottom:12px}
  .step-list{list-style:none}
  .step-list li{position:relative;padding:0 0 6px 11px;margin-bottom:7px;font-weight:500;font-size:11.3px;line-height:13.4px;border-bottom:1px solid var(--rule)}
  .step-list li:last-child{border-bottom:none;margin-bottom:0}
  .step-list li::before{content:"";position:absolute;left:0;top:4px;width:6px;height:6px;border-radius:50%;background:var(--navy)}
  .step-list--gold li::before{background:var(--yellow)}
  .step-close{font-weight:500;font-size:11.3px;line-height:13px;text-align:center;margin:6px -2px 0 -4px}
  .step-num{position:absolute;width:36px;height:36px;border-radius:50%;background:var(--white);border:3px solid var(--navy);top:181px;display:flex;align-items:center;justify-content:center;font-weight:800;font-size:20px;color:var(--navy)}

  .chev{position:absolute;font-weight:900;font-size:15px;color:var(--navy);letter-spacing:-3px}

  .motto-art{position:absolute;top:590px;width:70px;height:60px;border-radius:8px;background:linear-gradient(#eef3fb,#dbe6f5)}
  .motto{position:absolute;top:656px;width:120px;height:32px;border:3px solid var(--yellow);border-radius:8px;background:var(--white);display:flex;align-items:center;justify-content:center;font-weight:800;font-size:19px;color:var(--navy);letter-spacing:-.3px;white-space:nowrap}

  .footer-band{position:absolute;left:0;right:0;bottom:0;background:var(--navy-deep);color:var(--white)}
  .poster--help .footer-band{height:31px;padding:4px 0 0 23px;font-family:"Fira Sans Condensed",sans-serif;font-size:5.6px;line-height:11.5px;font-weight:500;white-space:nowrap;overflow:hidden}
  .poster--ai .footer-band{height:49px;display:flex;align-items:center;justify-content:center;font-weight:600;font-size:16.5px}

  /* AI poster */
  .panel{position:absolute;top:224px;width:225px;height:247px;background:var(--ice);border:3px solid var(--navy);border-top:none;border-radius:0 0 8px 8px;padding:0 4px 0 8px;display:flex;flex-direction:column}
  .panel-tab{position:absolute;top:191px;height:33px;background:var(--yellow);border-radius:0 4px 4px 0;display:flex;align-items:center;font-weight:600;font-size:17.5px;color:var(--navy);white-space:nowrap}
  .badge{position:absolute;width:42px;height:42px;border-radius:50%;background:var(--white);border:3px solid var(--navy);display:flex;align-items:center;justify-content:center}
  .badge svg{width:24px;height:24px}
  .row{flex:1;display:flex;align-items:center;gap:12px;border-bottom:1px solid var(--rule)}
  .row:last-child{border-bottom:none}
  .icon{flex:0 0 44px;height:40px;border-radius:8px;background:#d3e1f3}
  .row p{font-weight:500;font-size:13px;line-height:15.3px}

  .ban-box{position:absolute;left:24px;top:509px;width:479px;height:153px;background:var(--cream);border:3px solid var(--yellow);border-radius:10px;padding:22px 8px 6px 13px;display:grid;grid-template-columns:247px 1fr}
  .ban-tab{position:absolute;left:48px;top:491px;width:199px;height:35px;background:var(--navy);border:2px solid var(--yellow);border-left:none;border-radius:0 4px 4px 0;display:flex;align-items:center;padding-left:18px;font-weight:600;font-size:18px;color:var(--white);white-space:nowrap}
  .ban-item{display:flex;align-items:center;gap:13px;border-bottom:1px solid #d8cf9c;margin-right:12px}
  .ban-item:nth-child(even){margin-right:0;gap:12px}
  .ban-item:nth-child(n+3){border-bottom:none}
  .ban-item .icon{flex:0 0 60px;height:44px;background:#ece3bd}
  .ban-item:nth-child(even) .icon{flex-basis:55px}
  .ban-item p{font-weight:500;font-size:13px;line-height:15.3px}
</style>
</head>
<body>

<section class="poster poster--help" aria-label="Before you ask the teacher poster">
  <svg class="poster-bg" viewBox="0 0 524 741" preserveAspectRatio="none" aria-hidden="true">
    <defs><linearGradient id="navyFade" x1="0" y1="0" x2="0" y2="1"><stop offset="0" stop-color="#173676"/><stop offset="1" stop-color="#21499a"/></linearGradient></defs>
    <rect width="524" height="741" fill="url(#navyFade)"/>
    <path d="M0 451 Q262 380 524 451 L524 741 L0 741 Z" fill="#fff"/>
  </svg>

  <div class="brand"><span class="brand-mark"></span><span class="brand-name">CORVAL<br>HIGH</span></div>
  <h1 class="headline">Before you ask<br>the teacher...</h1>
  <p class="subhead">Try these steps first!</p>

  <article class="step" style="left:35px">
    <div class="step-art"><span role="img" aria-label="Icon of a head with a thinking brain"></span></div>
    <h2 class="step-label">Think<br>first</h2>
    <div class="step-body">
      <p class="step-lead">Don't give up straight away.</p>
      <ul class="step-list">
        <li>Read the question carefully.</li>
        <li>Identify what you already know.</li>
        <li>Try a strategy you've used before.</li>
        <li>Give yourself thinking time.</li>
      </ul>
    </div>
  </article>
  <article class="step" style="left:196px">
    <div class="step-art"><span role="img" aria-label="Icon of a checklist with a magnifying glass"></span></div>
    <h2 class="step-label">Check your<br>supports</h2>
    <div class="step-body" style="padding-right:1px">
      <p class="step-lead">Before asking for help, check</p>
      <ul class="step-list">
        <li>Learning goal and success criteria.</li>
        <li>Worked examples.</li>
        <li>Class notes.</li>
        <li>Classroom displays.</li>
        <li>ClassHub resources.</li>
        <li>Task sheet and instructions.</li>
      </ul>
    </div>
  </article>
  <article class="step" style="left:360px">
    <div class="step-art"><span role="img" aria-label="Icon of three people talking together"></span></div>
    <h2 class="step-label">Ask 3 before<br>me</h2>
    <div class="step-body" style="padding-top:7px">
      <p class="step-lead" style="margin-bottom:10px">Ask three sources before asking the teacher:</p>
      <ul class="step-list step-list--gold">
        <li>A person (partner or neighbour)</li>
        <li>A place (notes, display, ClassHub)</li>
        <li>A resource (worked example, task sheet)</li>
      </ul>
      <p class="step-close">Then ask the teacher if you still need help.</p>
    </div>
  </article>

  <span class="step-num" style="left:17px">1</span>
  <span class="step-num" style="left:180px">2</span>
  <span class="step-num" style="left:344px">3</span>

  <span class="chev" style="left:172px;top:430px">&#x276F;&#x276F;</span>
  <span class="chev" style="left:333px;top:431px">&#x276F;&#x276F;</span>

  <div class="motto-art" style="left:70px" role="img" aria-label="Illustration of two students standing together"></div>
  <div class="motto-art" style="left:232px" role="img" aria-label="Illustration of students climbing a hill"></div>
  <div class="motto-art" style="left:395px" role="img" aria-label="Illustration of students raising a flag on a summit"></div>

  <div class="motto" style="left:44px">WE BELIEVE</div>
  <span class="chev" style="left:173px;top:663px">&#x276F;&#x276F;</span>
  <div class="motto" style="left:202px">WE STRIVE</div>
  <span class="chev" style="left:334px;top:663px">&#x276F;&#x276F;</span>
  <div class="motto" style="left:365px">WE ACHIEVE</div>

  <footer class="footer-band">
    Hartwell, C. (2025). "Why Students Don't Ask for Help - And How to Change That." Downloaded on 24/04/2026 from https://www.classroomnotes.example/article/getting-students-ask-help/<br>
    ERTA. (2024). "Supporting Self-Regulated Learning." Downloaded on 24/04/2026 from https://www.evidenceinstitute.example/sites/default/files/2024-02/supporting-self-regulated-learning.pdf
  </footer>
</section>

<section class="poster poster--ai" aria-label="Using AI responsibly poster">
  <svg class="poster-bg" viewBox="0 0 524 741" preserveAspectRatio="none" aria-hidden="true">
    <defs><linearGradient id="navyFade2" x1="0" y1="0" x2="0" y2="1"><stop offset="0" stop-color="#173676"/><stop offset="1" stop-color="#21499a"/></linearGradient></defs>
    <rect width="524" height="741" fill="url(#navyFade2)"/>
    <path d="M0 451 Q262 380 524 451 L524 741 L0 741 Z" fill="#fff"/>
  </svg>

  <div class="brand"><span class="brand-mark"></span><span class="brand-name">CORVAL<br>HIGH</span></div>
  <h1 class="headline">Using AI and other<br>tools responsibly</h1>
  <p class="subhead">Responsible AI starts with<br>responsible learners</p>

  <div class="panel-tab" style="left:38px;width:212px;padding-left:31px">What you must do</div>
  <div class="panel" style="left:26px">
    <div class="row"><span class="icon" role="img" aria-label="Icon of a student writing at a desk"></span><p>Complete your own work</p></div>
    <div class="row"><span class="icon" role="img" aria-label="Icon of notes and a pencil"></span><p>Demonstrate your progress (drafts, notes, planning, revisions)</p></div>
    <div class="row"><span class="icon" role="img" aria-label="Icon of people giving feedback"></span><p>Use feedback to improve your work</p></div>
    <div class="row"><span class="icon" role="img" aria-label="Icon of a person with a light bulb idea"></span><p>Demonstrate your understanding of the ideas in your submission</p></div>
  </div>
  <div class="badge" style="left:17px;top:186px"><svg viewBox="0 0 24 24" aria-hidden="true"><path d="M4 12.5l5 5L20 6" fill="none" stroke="#1a3a7c" stroke-width="3.4" stroke-linecap="round" stroke-linejoin="round"/></svg></div>

  <div class="panel-tab" style="left:281px;width:228px;padding-left:30px">What AI can help you do</div>
  <div class="panel" style="left:272px">
    <div class="row"><span class="icon" role="img" aria-label="Icon of a brain"></span><p>Brainstorm ideas</p></div>
    <div class="row"><span class="icon" role="img" aria-label="Icon of a document with a tick"></span><p>Check spelling, gram&shy;mar and clarity</p></div>
    <div class="row"><span class="icon" role="img" aria-label="Icon of a speaker in a speech bubble"></span><p>Read your work aloud using text-to-speech tools</p></div>
    <div class="row"><span class="icon" role="img" aria-label="Icon of a document under a magnifying glass"></span><p>Help identify areas for improvement in a draft</p></div>
  </div>
  <div class="badge" style="left:260px;top:186px"><svg viewBox="0 0 24 24" aria-hidden="true"><path d="M4 12.5l5 5L20 6" fill="none" stroke="#1a3a7c" stroke-width="3.4" stroke-linecap="round" stroke-linejoin="round"/></svg></div>

  <div class="ban-box">
    <div class="ban-item"><span class="icon" role="img" aria-label="Icon of a computer producing a document"></span><p>Submit AI-generated work as your own</p></div>
    <div class="ban-item"><span class="icon" role="img" aria-label="Icon of a robot completing a checklist"></span><p>Use AI tools to com&shy;plete the whole task for you</p></div>
    <div class="ban-item"><span class="icon" role="img" aria-label="Icon of copied documents"></span><p>Copy and paste AI respons&shy;es without acknowledging or adapting them</p></div>
    <div class="ban-item"><span class="icon" role="img" aria-label="Icon of a person with a question"></span><p>Submit work that does not demonstrate your understanding</p></div>
  </div>
  <div class="ban-tab">What you cannot&nbsp; do</div>
  <div class="badge" style="left:17px;top:488px"><svg viewBox="0 0 24 24" aria-hidden="true"><path d="M5 5l14 14M19 5L5 19" fill="none" stroke="#1a3a7c" stroke-width="3.4" stroke-linecap="round"/></svg></div>

  <footer class="footer-band">If you didn't create, develop and understand it, it isn't your work.</footer>
</section>

</body>
</html>
```